Floor Inspections and Consulting

We provide inspections and consulting services on various floor coverings, e.g. carpet, hardwood, etc. We also do expert witness work for attorneys due to floor covering failures. We current have a logo, just need it incorporated into a new design. I have examples of cards I have found on the internet that capture my attention and make a statement. I have included our original business card, which in my opinion is terrible, but it does have our logo on it.

```html
<!DOCTYPE html>
<html lang="en">
<head>
<meta charset="utf-8">
<title>Northfield Floor Inspections – Business Card</title>
<link rel="stylesheet" href="https://fonts.googleapis.com/css2?family=Open+Sans:wdth,wght@75..100,400..700&display=swap">
<style>
  :root {
    --purple: #7e2a92;
    --purple-light: #a24fb4;
    --ink: #061822;
    --graphite: #3a4046;
    --white: #ffffff;
    --backdrop: #ecebea;
  }
  * { box-sizing: border-box; margin: 0; padding: 0; }
  html, body { width: 1200px; height: 900px; overflow: hidden; }
  body {
    background: var(--backdrop);
    font-family: "Open Sans", Arial, sans-serif;
    color: var(--white);
  }
  .sheet { position: relative; width: 1200px; height: 900px; }
  .card {
    position: absolute;
    top: 137px;
    width: 360px;
    height: 626px;
    overflow: hidden;
    box-shadow: 0 10px 30px rgba(0,0,0,.18);
  }
  .card--front { left: 205px; background: var(--purple); }
  .card--back { left: 635px; background: var(--ink); }
  .card__art { position: absolute; inset: 0; width: 360px; height: 626px; }

  .brand {
    position: absolute;
    left: 0; right: 0;
    display: flex;
    align-items: center;
    justify-content: center;
    gap: 12px;
    font-weight: 700;
    text-transform: uppercase;
    line-height: 1.15;
    color: var(--white);
  }
  .brand__dot { border-radius: 50%; background: var(--white); flex: none; }
  .card--front .brand { top: 110px; font-size: 21px; letter-spacing: 1px; }
  .card--front .brand__dot { width: 26px; height: 26px; }
  .card--back .brand { top: 185px; font-size: 15px; letter-spacing: .8px; }
  .card--back .brand__dot { width: 18px; height: 18px; }

  .tagline {
    position: absolute;
    left: 0; right: 0;
    text-align: center;
    text-transform: uppercase;
    font-stretch: 88%;
    font-weight: 400;
  }
  .card--front .tagline { top: 238px; font-size: 17px; letter-spacing: .3px; }
  .card--back .tagline { top: 58px; font-size: 16px; line-height: 1.5; }

  .holder {
    position: absolute;
    left: 42px;
    bottom: 72px;
    font-size: 32px;
    font-weight: 600;
    font-stretch: 80%;
    letter-spacing: .2px;
    line-height: 1;
  }
  .holder__last { color: var(--purple-light); }
  .holder__rule {
    position: absolute;
    left: 42px;
    bottom: 60px;
    width: 276px;
    height: 3px;
    background: var(--white);
  }
  .holder__rule::after {
    content: "";
    position: absolute;
    left: 0; top: 3px;
    width: 110px; height: 4px;
    background: var(--purple);
  }

  .contact {
    position: absolute;
    left: 36px;
    bottom: 42px;
    list-style: none;
    font-size: 15px;
    font-stretch: 90%;
  }
  .contact__item { display: flex; align-items: center; gap: 10px; margin-top: 8px; }
  .contact__icon { width: 16px; height: 16px; flex: none; }
</style>
</head>
<body>
<main class="sheet">

  <section class="card card--front" aria-label="Business card front">
    <svg class="card__art" viewBox="0 0 360 626" aria-hidden="true">
      <defs>
        <linearGradient id="band-purple" x1="0" y1="0" x2="1" y2="1">
          <stop offset="0" stop-color="#b062c2"/>
          <stop offset="1" stop-color="#8d3aa1"/>
        </linearGradient>
      </defs>
      <polygon points="0,300 180,420 360,300 360,626 0,626" fill="var(--ink)"/>
    </svg>
    <svg class="card__art" viewBox="0 0 360 626" role="img" aria-label="Faceted pyramid pattern band in purple tones">
      <polygon points="0,270 180,385 360,270 360,335 180,450 0,335" fill="url(#band-purple)"/>
    </svg>
    <svg class="card__art" viewBox="0 0 360 626" role="img" aria-label="Fine line triangle grid pattern">
      <polygon points="0,375 130,470 0,560" fill="#162630"/>
    </svg>

    <div class="brand"><span class="brand__dot"></span><span>Northfield<br>Floor Inspections</span></div>
    <p class="tagline">Analysis &amp; Consulting</p>

    <h1 class="holder">DANA <span class="holder__last">HOLLOWAY</span></h1>
    <div class="holder__rule"></div>
  </section>

  <section class="card card--back" aria-label="Business card back">
    <svg class="card__art" viewBox="0 0 360 626" aria-hidden="true">
      <defs>
        <linearGradient id="band-graphite" x1="0" y1="0" x2="1" y2="1">
          <stop offset="0" stop-color="#4a5056"/>
          <stop offset="1" stop-color="#1e262c"/>
        </linearGradient>
      </defs>
      <polygon points="0,360 180,480 360,360 360,626 0,626" fill="var(--purple)"/>
    </svg>
    <svg class="card__art" viewBox="0 0 360 626" role="img" aria-label="Faceted pyramid pattern band in graphite tones">
      <polygon points="0,300 180,415 360,300 360,355 180,470 0,355" fill="url(#band-graphite)"/>
    </svg>
    <svg class="card__art" viewBox="0 0 360 626" role="img" aria-label="Fine line triangle grid pattern">
      <polygon points="360,395 240,480 360,570" fill="#8f3fa3"/>
    </svg>

    <p class="tagline">Certified Floor Covering<br>Inspections &amp; Consulting</p>
    <div class="brand"><span class="brand__dot"></span><span>Northfield<br>Floor Inspections</span></div>

    <ul class="contact">
      <li class="contact__item">
        <svg class="contact__icon" viewBox="0 0 16 16" aria-hidden="true"><circle cx="8" cy="8" r="7" fill="none" stroke="#fff" stroke-width="1.2"/><path d="M5.5 4.5l1.3 1.6-.8.9c.6 1.2 1.5 2.1 2.7 2.7l.9-.8 1.6 1.3-.9 1.2c-2.6-.4-4.8-2.6-5.2-5.2z" fill="#fff"/></svg>
        <span>303-555-0147</span>
      </li>
      <li class="contact__item">
        <svg class="contact__icon" viewBox="0 0 16 16" aria-hidden="true"><rect x="1.5" y="3.5" width="13" height="9" fill="none" stroke="#fff" stroke-width="1.2"/><path d="M1.5 3.5l6.5 5 6.5-5" fill="none" stroke="#fff" stroke-width="1.2"/></svg>
        <span>dana@northfieldfloors.com</span>
      </li>
      <li class="contact__item">
        <svg class="contact__icon" viewBox="0 0 16 16" aria-hidden="true"><g fill="none" stroke="#fff" stroke-width="1.1"><circle cx="8" cy="8" r="6.5"/><ellipse cx="8" cy="8" rx="3" ry="6.5"/><path d="M1.5 8h13M2.5 5h11M2.5 11h11"/></g></svg>
        <span>northfieldfloors.com</span>
      </li>
    </ul>
  </section>

</main>
</body>
</html>
```